Varnel Corporate Website for technological company

We need a modern website to promote our product and services.
You can found the actually website at the address: www.varnel-example.ch

We are a new company for B2B market. We would like do show our high precision and innovation capability.

we need a section were is possible to easily upload "news" and documents for our customers.

Target Market(s)

B2B services in the industry market

Industry/Entity Type

It Company

Coding

Coded - Design and coding required

Number of Pages Required

5+ page

Font styles to use
Other font styles liked:
• We accept propositions

Requirements
Must have
• Easy to maintain
• Presentation of the Varnel company
• Presentation of Varnel services and products
• The customer can download our ducumentation
Nice to have
• Sexy and modern

```html
<!DOCTYPE html>
<html lang="en">
<head>
<meta charset="utf-8">
<title>Varnel Sagl</title>
<link href="https://fonts.googleapis.com/css2?family=Open+Sans:wght@400;600;700;800&display=swap" rel="stylesheet">
<style>
:root{
  --gold:#a39a4a;
  --gold-light:#b9b063;
  --gold-dark:#8f8740;
  --ink:#333;
  --text:#555;
  --muted:#888;
  --soft-bg:#f4f5f7;
  --line:#e2e2e2;
  --footer:#2b2b2b;
  --footer-bottom:#1f1f1f;
  --white:#fff;
}
*{margin:0;padding:0;box-sizing:border-box}
html,body{width:1200px;height:2353px;overflow:hidden}
body{font-family:'Open Sans',Arial,sans-serif;color:var(--text);background:var(--white);position:relative}
.abs{position:absolute}
/* header */
.topline{left:0;top:0;width:1200px;height:3px;background:var(--gold)}
.brand{left:130px;top:40px;display:flex;align-items:flex-end;gap:10px}
.brand-mark{width:44px;height:44px;background:var(--gold);align-self:center}
.brand-name{font-weight:800;font-size:52px;line-height:1;color:#1c1c1c;letter-spacing:1px}
.lang{left:806px;top:58px;width:54px;height:28px;border:1px solid #ccc;border-radius:3px;font-size:12px;color:#333;display:flex;align-items:center;justify-content:center;gap:6px}
.search{left:872px;top:55px;width:196px;height:32px;border:1px solid #ccc;border-radius:3px;display:flex}
.search span{flex:1;font-size:11px;color:#555;padding:8px 12px}
.search i{width:36px;background:var(--gold);display:flex;align-items:center;justify-content:center}
/* nav */
.nav{left:0;top:138px;width:1200px;height:46px;background:linear-gradient(var(--gold-light),var(--gold-dark))}
.nav ul{list-style:none;display:flex;margin-left:132px;height:46px}
.nav li{font-size:11px;color:var(--white);padding:0 24px;display:flex;align-items:center;border-right:1px solid rgba(255,255,255,.25)}
.nav li.active{background:#1d1d1d;padding:0 24px}
/* hero */
.hero{left:0;top:184px;width:1200px;height:404px;background:linear-gradient(90deg,#3b3d42 0%,#56585d 40%,#7a7b7c 60%,#3e5d86 100%)}
.hero-title{left:132px;top:270px;font-size:40px;font-weight:600;color:var(--white)}
.hero-text{left:132px;top:333px;width:330px;font-size:12.5px;line-height:20px;color:var(--white)}
.btn{background:var(--gold);color:var(--white);font-size:12px;display:flex;align-items:center;justify-content:center;border-radius:2px}
.hero-btn{left:132px;top:397px;width:96px;height:38px}
.dots{left:130px;top:459px;display:flex;gap:6px}
.dots b{width:12px;height:12px;border-radius:50%;background:var(--white)}
.dots b:first-child{border:2px solid var(--gold)}
/* welcome */
.section-title{left:0;width:1200px;text-align:center;font-size:30px;color:var(--ink);font-weight:400}
.welcome-text{left:132px;top:676px;width:936px;text-align:justify;text-align-last:center;font-size:12px;line-height:19px;color:#444}
.welcome-btn{left:549px;top:751px;width:101px;height:40px}
.services{left:0;top:858px;width:1200px;height:452px;background:var(--soft-bg);border-top:1px solid var(--line)}
.service{width:220px;text-align:center}
.service .ring{width:116px;height:116px;border-radius:50%;border:3px solid #ddd;margin:0 auto;display:flex;align-items:center;justify-content:center;background:var(--white)}
.service.active .ring{border-color:var(--gold)}
.service h3{font-size:20px;font-weight:400;color:var(--ink);margin-top:35px}
.service p{font-size:11.5px;line-height:19px;color:#555;margin-top:14px;text-align:justify;text-align-last:center}
/* testimonial */
.testimonial{left:0;top:1310px;width:1200px;height:273px;background:linear-gradient(#3f4854,#555b62 55%,#4a4e52)}
.avatar{left:535px;top:1338px;width:110px;height:110px;border-radius:50%;border:4px solid var(--white);background:linear-gradient(#c9a58f,#8a6c5c)}
.quote{left:200px;top:1473px;width:800px;text-align:center;font-size:12px;line-height:19px;color:var(--white);font-style:italic}
.quote-name{left:0;top:1522px;width:1200px;text-align:center;font-size:12px;color:var(--white);font-style:italic}
.arrow{top:1435px}
/* news */
.card{width:286px}
.card .photo{height:160px;border:6px solid var(--white);outline:1px solid #ddd}
.card h4{font-size:19.5px;font-weight:400;color:var(--ink);margin-top:26px;white-space:nowrap}
.card p{font-size:11.5px;line-height:19px;color:#555;margin-top:12px;text-align:justify}
.card p a{color:var(--gold);text-decoration:none}
/* footer */
.footer{left:0;top:2046px;width:1200px;height:245px;background:var(--footer)}
.footer-bottom{left:0;top:2291px;width:1200px;height:62px;background:var(--footer-bottom)}
.footer-brand{left:132px;top:2084px;display:flex;align-items:center;gap:10px}
.footer-brand .brand-mark{width:38px;height:38px;background:#777}
.footer-brand .brand-name{font-size:44px;color:#1a1a1a}
.socials{left:132px;top:2174px;display:flex;gap:7px}
.socials b{width:30px;height:30px;border-radius:50%;border:2px solid var(--white)}
.f-head{font-size:15px;color:var(--white)}
.f-list{list-style:none;font-size:11px;color:var(--white);line-height:21px}
.newsletter-text{left:645px;top:2118px;font-size:11px;color:#ddd}
.email{left:645px;top:2151px;width:195px;height:35px;background:#4a4a4a;color:#ddd;font-size:11px;padding:11px 10px}
.subscribe{left:645px;top:2204px;width:83px;height:30px;font-size:11px}
.contact-list{left:932px;top:2113px;list-style:none;font-size:11px;color:var(--white)}
.contact-list li{display:flex;gap:12px;align-items:flex-start;height:28px;line-height:16px}
.contact-list svg{flex:none;margin-top:2px}
.contact-list a{color:var(--white)}
.copyright{left:132px;top:2314px;font-size:11px;color:#ddd}
.mini-socials{left:949px;top:2312px;display:flex;gap:12px}
.mini-socials b{width:13px;height:13px;background:#ddd;border-radius:2px}
</style>
</head>
<body>
<div class="abs topline"></div>
<header>
  <div class="abs brand"><span class="brand-mark"></span><span class="brand-name">VARNEL Sagl</span></div>
  <div class="abs lang">EN <svg width="8" height="6" viewBox="0 0 8 6"><path d="M1 1l3 3 3-3" stroke="#333" fill="none" stroke-width="1.4"/></svg></div>
  <div class="abs search"><span>Search</span><i><svg width="14" height="14" viewBox="0 0 14 14"><circle cx="6" cy="6" r="4.5" stroke="#fff" stroke-width="2" fill="none"/><path d="M9.3 9.3L13 13" stroke="#fff" stroke-width="2"/></svg></i></div>
</header>
<nav class="abs nav"><ul>
  <li class="active">HOME</li><li>SERVICES</li><li>PRODUCTS</li><li>EXAMPLES</li><li>DOWNLOAD</li><li>CONTACTS</li>
</ul></nav>

<section>
  <div class="abs hero" role="img" aria-label="Photo of hands joining coloured puzzle pieces"></div>
  <h1 class="abs hero-title">Modern Systems</h1>
  <p class="abs hero-text">VARNEL Ltd. designs systems in which electronics, software and mechanics are perfectly integrated</p>
  <div class="abs btn hero-btn">View Details</div>
  <div class="abs dots"><b></b><b></b><b></b></div>
</section>

<section>
  <h2 class="abs section-title" style="top:615px">WELCOME TO VARNEL</h2>
  <p class="abs welcome-text">The ever-increasing complexity in modern systems, the search for reliability and performance and the continuous desire to reduce production costs and dimensions of the products require a rigorous integration between the electronic units, software and mechanical systems.VARNEL Ltd. designs systems in which electronics, software and mechanics are perfectly integrated to achieve uncompromising performance.</p>
  <div class="abs btn welcome-btn">Read More</div>
</section>

<section class="abs services"></section>
<h2 class="abs section-title" style="top:899px">OUR SERVICES</h2>
<div class="abs service active" style="left:125px;top:987px">
  <div class="ring"><svg width="36" height="30" viewBox="0 0 36 30"><path d="M4 11h6l16-8v24l-16-8H4z" fill="#a39a4a"/><path d="M9 19l3 8h4l-3-8" fill="#a39a4a"/></svg></div>
  <h3>SIMULATION</h3><p>Neque porro quisquam est qui dolorem ipsum quia dolor sit amet, consectetur, adipisci velit...</p>
</div>
<div class="abs service" style="left:370px;top:987px">
  <div class="ring"><svg width="20" height="34" viewBox="0 0 20 34"><path d="M12 1L3 19h7l-3 14 10-20h-7z" fill="#999"/></svg></div>
  <h3>ELECTRONICS</h3><p>Neque porro quisquam est qui dolorem ipsum quia dolor sit amet, consectetur, adipisci velit...</p>
</div>
<div class="abs service" style="left:613px;top:987px">
  <div class="ring"><svg width="42" height="36" viewBox="0 0 42 36"><circle cx="15" cy="20" r="10" fill="none" stroke="#999" stroke-width="6" stroke-dasharray="4 3"/><circle cx="15" cy="20" r="4" fill="#999"/><circle cx="32" cy="9" r="6" fill="none" stroke="#999" stroke-width="4" stroke-dasharray="3 2"/></svg></div>
  <h3>MECHANICS</h3><p>Neque porro quisquam est qui dolorem ipsum quia dolor sit amet, consectetur, adipisci velit...</p>
</div>
<div class="abs service" style="left:855px;top:987px">
  <div class="ring"><svg width="40" height="34" viewBox="0 0 40 34"><rect x="1" y="1" width="38" height="24" rx="2" fill="#999"/><rect x="5" y="5" width="30" height="16" fill="#fff"/><rect x="15" y="25" width="10" height="5" fill="#999"/><rect x="10" y="30" width="20" height="3" fill="#999"/></svg></div>
  <h3>SOFTWARE</h3><p>Neque porro quisquam est qui dolorem ipsum quia dolor sit amet, consectetur, adipisci velit...</p>
</div>

<section>
  <div class="abs testimonial" role="img" aria-label="Photo of a city skyline seen from above"></div>
  <div class="abs avatar" role="img" aria-label="Portrait photo of the client quoted"></div>
  <svg class="abs arrow" style="left:134px" width="20" height="46" viewBox="0 0 20 46"><path d="M18 2L2 23l16 21" stroke="#fff" stroke-width="1.5" fill="none"/></svg>
  <svg class="abs arrow" style="left:1046px" width="20" height="46" viewBox="0 0 20 46"><path d="M2 2l16 21L2 44" stroke="#fff" stroke-width="1.5" fill="none"/></svg>
  <p class="abs quote">" Nemo enim ipsam voluptatem quia voluptas sit aspernatur aut odit aut fugit, sed quia consequuntur magni dolores eos qui ratione voluptatem sequi nesciunt. Neque porro quisquam est, qui dolorem ipsum quia dolor sit amet, consectetur "</p>
  <p class="abs quote-name">- Alex Marin -</p>
</section>

<section>
  <h2 class="abs section-title" style="top:1627px">RECENT NEWS</h2>
  <article class="abs card" style="left:130px;top:1709px">
    <div class="photo" role="img" aria-label="Photo of machined metal components" style="background:linear-gradient(#8f969c,#c4c8cc)"></div>
    <h4>Added the 'application' page</h4>
    <p>Lorem ipsum dolor sit amet, consectetur adipiscing elit, sed do eiusmod tempor incididunt ut labore et dolore magna aliqua. <a>Read More »</a></p>
  </article>
  <article class="abs card" style="left:458px;top:1709px">
    <div class="photo" role="img" aria-label="Photo of a support agent with a headset" style="background:linear-gradient(90deg,#dfe6ec,#b9c4cf)"></div>
    <h4>In download page are availables</h4>
    <p>Lorem ipsum dolor sit amet, consectetur adipiscing elit, sed do eiusmod tempor incididunt ut labore et dolore magna aliqua. <a>Read More »</a></p>
  </article>
  <article class="abs card" style="left:785px;top:1709px">
    <div class="photo" role="img" aria-label="Photo of a CNC milling machine" style="background:linear-gradient(90deg,#9aa2aa,#dcdfe2,#7d858c)"></div>
    <h4>Varnel Ltd., wish</h4>
    <p>Lorem ipsum dolor sit amet, consectetur adipiscing elit, sed do eiusmod tempor incididunt ut labore et dolore magna aliqua. <a>Read More »</a></p>
  </article>
</section>

<footer>
  <div class="abs footer"></div>
  <div class="abs footer-brand"><span class="brand-mark"></span><span class="brand-name">VARNEL</span></div>
  <div class="abs socials"><b></b><b></b><b></b><b></b><b></b></div>
  <h5 class="abs f-head" style="left:461px;top:2080px;font-weight:400">Quick Links</h5>
  <ul class="abs f-list" style="left:461px;top:2110px"><li>Home</li><li>Services</li><li>Products</li><li>Examples</li><li>Download</li><li>Contacts</li></ul>
  <h5 class="abs f-head" style="left:645px;top:2080px;font-weight:400">Newsletter</h5>
  <p class="abs newsletter-text">Sign Up for Our Newsletter &amp; Promotion</p>
  <div class="abs email">Enter Your email Id</div>
  <div class="abs btn subscribe">SUBSCRIBE</div>
  <h5 class="abs f-head" style="left:932px;top:2080px;font-weight:400">Contact Us</h5>
  <ul class="abs contact-list">
    <li><svg width="13" height="12" viewBox="0 0 13 12"><path d="M1 4c0-2 2-3 5.5-3S12 2 12 4l-3 1-1-2H5L4 5zM3 6h7l1 5H2z" fill="#fff"/></svg>+41 (0)00 555 01 23</li>
    <li><svg width="13" height="12" viewBox="0 0 13 12"><rect x="3" y="0" width="7" height="4" fill="#fff"/><rect x="0" y="4" width="13" height="5" fill="#fff"/><rect x="3" y="8" width="7" height="4" fill="#fff"/></svg>+41 (0)00 555 01 23</li>
    <li><svg width="13" height="10" viewBox="0 0 13 10"><rect x="0.5" y="0.5" width="12" height="9" fill="none" stroke="#fff"/><path d="M1 1l5.5 5L12 1" stroke="#fff" fill="none"/></svg><a>info@varnel.ch</a></li>
    <li><svg width="13" height="14" viewBox="0 0 13 14"><path d="M6.5 0a5 5 0 0 1 5 5c0 4-5 9-5 9s-5-5-5-9a5 5 0 0 1 5-5z" fill="#fff"/><circle cx="6.5" cy="5" r="2" fill="#2b2b2b"/></svg><span>Chemin des Tilleuls 7<br>CH - 1000 Lindenau</span></li>
  </ul>
  <div class="abs footer-bottom"></div>
  <p class="abs copyright">Copyright © 2016 varnel.ch. All Right Reserved.</p>
  <div class="abs mini-socials"><b></b><b></b><b></b><b></b><b></b></div>
</footer>
</body>
</html>
```